Sci Fi/ Secret Agent Author needs website design!

My name is Lark Whitby and I am an author. I require a site that can provide information about myself and my books and other works.

I would like it to have a Home, blog function, (about the) books/series section so people can visit another section and read about each individual book that's going to be released. A resources page, a Store, social media links and ability to load/embed videos from clipvane and other.

I write mild scifi/thriller/conspiracy/secret government type novels. -At the moment-. The series follows a strong female lead that is an agent with a secret organisation in a classified military installation.

The theme would be professional yet possibly show this element.

/military fiction/thriller/fantasy/Sci fi/ femme-fatal, readers. Mostly females, age 18-60
Novel readers

5+ page

• Would like designers to follow brief. :)
• My budget includes all the pages I will need;
• eg home, blog, resources, store, ability to pay with coinpouch and Credit Cards
• , ability to have trailers from clipvane etc. Must have links to the social media mentioned in the brief.
• use of the colours I have suggested. electric/indigo purple, fuschia highlights , dark greys
• as I will possibly base branding for social media ETC on the look of your website design and colour scheme.
• Ability for trailer on front page??
• Should not be too cluttered. (But I am open to all ideas)

```html
<!DOCTYPE html>
<html lang="en">
<head>
<meta charset="utf-8">
<title>Lark Whitby — Author</title>
<link href="https://fonts.googleapis.com/css2?family=Jost:wght@400;500&family=Open+Sans:wght@400;600;700&display=swap" rel="stylesheet">
<style>
:root{
  --purple:#7000b5;
  --purple-deep:#3f0079;
  --purple-dark:#2a0058;
  --fuchsia:#b012c8;
  --ink:#1c1c1c;
  --grey-text:#555;
  --grey-light:#e7e7e9;
  --grey-band:#d9d9db;
  --white:#fff;
}
*{box-sizing:border-box;margin:0;padding:0}
html,body{width:1200px;height:2293px;overflow:hidden;background:var(--white)}
body{position:relative;font-family:'Open Sans',sans-serif;color:var(--grey-text)}
.abs{position:absolute}
.topbar{left:0;top:0;width:1200px;height:46px;background:var(--grey-light)}
.social{display:flex;gap:6px;align-items:center}
.social span{display:flex;align-items:center;gap:3px;font-family:'Jost',sans-serif;font-size:11px;color:#444}
.social span::before{content:"";width:8px;height:8px;border:1px solid #444;border-radius:50%}
.topbar .social{left:118px;top:15px}
.cart{right:116px;top:12px;display:flex;align-items:center;gap:8px;font-family:'Jost',sans-serif;font-size:15px;color:var(--purple-deep)}
.header{left:0;top:46px;width:1200px;height:102px;background:var(--white)}
.logo{left:115px;top:22px;font-family:'Jost',sans-serif;font-size:42px;color:var(--ink);letter-spacing:.5px}
.nav{top:38px;font-family:'Jost',sans-serif;font-size:18px;color:#666}
.nav a{position:absolute;color:inherit;text-decoration:none;white-space:nowrap}
.nav a.active{color:var(--purple-deep)}
.nav a.active::after{content:"";position:absolute;left:-2px;right:-2px;top:33px;height:2px;background:var(--purple)}
.hero{left:0;top:148px;width:1200px;height:532px;background:radial-gradient(ellipse at 10% 85%,#b21ed0 0%,rgba(178,30,208,0) 45%),linear-gradient(100deg,#8a1bb8 0%,#6a0aa8 45%,#4a0a8c 80%,#5a0aa0 100%)}
.badge{left:122px;top:135px;width:160px;height:35px;background:#6a0fd0;color:var(--white);font-family:'Jost',sans-serif;font-size:18px;line-height:35px;text-align:center}
.hero-title{left:122px;top:185px;width:440px;font-family:'Jost',sans-serif;font-size:29px;line-height:39px;color:var(--white)}
.hero-text{left:122px;top:278px;width:400px;font-size:15.5px;line-height:23px;color:#eee}
.hero-date{left:122px;top:340px;font-family:'Jost',sans-serif;font-size:16px;color:var(--white)}
.hero-book{left:757px;top:71px;width:211px;height:347px;background:linear-gradient(90deg,#d8d8d8,#ffffff 25%,#f2f2f2);box-shadow:6px 8px 14px rgba(0,0,0,.35)}
.dots{left:524px;top:488px;display:flex;gap:8px}
.dots i{display:block;width:32px;height:3px;background:var(--white)}
.dots i.on{background:#9a2ee0}
.about-photo{left:138px;top:696px;width:397px;height:471px;background:linear-gradient(180deg,#f3ede8 0%,#c9a58a 35%,#5a4a4f 75%,#3d3540 100%)}
.about-title{left:587px;top:778px;font-family:'Jost',sans-serif;font-size:31px;color:#333}
.about-text{left:587px;top:843px;width:490px;font-size:14.5px;line-height:29px;color:#555}
.about-text p+p{margin-top:12px}
.btn-outline{left:589px;top:1027px;width:154px;height:42px;border:2px solid var(--purple-deep);color:var(--purple-deep);font-family:'Jost',sans-serif;font-size:15px;line-height:38px;text-align:center}
.books{left:0;top:1167px;width:1200px;height:463px;background:linear-gradient(135deg,#e4e4e4,#cfcfcf 50%,#e2e2e2)}
.section-title{left:0;width:1200px;text-align:center;font-family:'Jost',sans-serif;font-size:29px;color:var(--purple)}
.cover{top:122px;width:212px;height:255px;border:4px solid var(--white);box-shadow:0 2px 6px rgba(0,0,0,.25)}
.caption{top:393px;width:212px;display:flex;justify-content:space-between;padding:0 8px;font-family:'Jost',sans-serif;font-size:16px;color:#666}
.caption b{font-weight:500;color:var(--purple)}
.newsletter{left:0;top:1630px;width:1200px;height:106px;background:var(--purple)}
.newsletter h2{position:absolute;left:176px;top:32px;font-family:'Jost',sans-serif;font-weight:400;font-size:28px;color:var(--white)}
.email{left:498px;top:29px;width:384px;height:38px;background:#a04cd2;color:#f1e6f8;font-size:14.5px;line-height:38px;padding-left:18px}
.subscribe{left:891px;top:29px;width:129px;height:38px;background:var(--purple-dark);color:var(--white);font-size:15px;font-weight:700;line-height:38px;text-align:center}
.tile{top:1806px;width:301px;height:241px}
.tile h3{position:absolute;left:0;top:92px;width:100%;text-align:center;font-family:'Jost',sans-serif;font-weight:400;font-size:27px;color:var(--white)}
.tile .band{position:absolute;left:0;top:136px;width:100%;height:31px;font-family:'Jost',sans-serif;font-size:16px;line-height:31px;text-align:center;color:var(--white)}
.footer{left:0;top:2141px;width:1200px;height:152px;background:var(--grey-band)}
.footer-nav{left:130px;top:36px;display:flex;gap:36px;font-family:'Jost',sans-serif;font-size:18px;color:#222}
.copyright{left:130px;top:73px;font-size:13px;color:#444}
.footer .social{right:130px;top:42px}
.footer .social span{font-size:12px;color:#111}
</style>
</head>
<body>

<div class="abs topbar">
  <div class="abs social"><span>Flitter</span><span>Pagebook</span><span>Linkwork</span><span>Orbitplus</span></div>
  <div class="abs cart">
    <svg width="26" height="22" viewBox="0 0 26 22" fill="none" stroke="#333" stroke-width="1.6"><path d="M1 2h4l3 12h13l3-9H7"/><circle cx="10" cy="19" r="1.6"/><circle cx="19" cy="19" r="1.6"/></svg>
    <span>0 items</span>
  </div>
</div>

<header class="abs header">
  <div class="abs logo">Lark Whitby</div>
  <nav class="abs nav" style="left:0">
    <a class="active" style="left:500px">Home</a>
    <a style="left:586px">Books</a>
    <a style="left:670px">Blog</a>
    <a style="left:743px">Resources</a>
    <a style="left:861px">Other works</a>
    <a style="left:997px">Store</a>
  </nav>
</header>

<section class="abs hero">
  <div class="abs badge">LATEST POSTS</div>
  <h1 class="abs hero-title" style="font-weight:400">Class aptent taciti sociosquad litora torquent conubia</h1>
  <p class="abs hero-text">Ut ac mi quis lacus mollis aliquam Curabitur iaculis tempus eros Curabitur vel mi sit amet magna</p>
  <p class="abs hero-date">Posted 05 May 2017</p>
  <div class="abs hero-book" role="img" aria-label="Hardcover book with a secret agent cover"></div>
  <div class="abs dots"><i></i><i></i><i class="on"></i><i></i></div>
</section>

<section>
  <div class="abs about-photo" role="img" aria-label="Portrait photo of the author"></div>
  <h2 class="abs about-title" style="font-weight:400">Little About Me</h2>
  <div class="abs about-text">
    <p>My name is Lark Whitby and I am an author. I require a site that can provide information about myself and my books and other works.</p>
    <p>I would like it to have a Home, blog function, about the books/series section, resources page, a Store, social media links and ability to load/embed videos from clipvane and other.</p>
  </div>
  <div class="abs btn-outline">READ MORE</div>
</section>

<section class="abs books">
  <h2 class="abs section-title" style="top:40px;font-weight:400">Books &amp; Novels</h2>
  <div class="abs cover" style="left:138px;background:radial-gradient(circle at 50% 50%,#222 0%,#444 30%,#f4f4f4 55%)" role="img" aria-label="Book cover with black sale splash"></div>
  <div class="abs cover" style="left:373px;background:linear-gradient(180deg,#b55a2a 0%,#7e8c74 35%,#5e7a68 100%)" role="img" aria-label="Western book cover with rider on horse"></div>
  <div class="abs cover" style="left:609px;background:radial-gradient(circle at 35% 75%,#c8502a 0%,#e9b89a 35%,#eae4d4 65%)" role="img" aria-label="Book cover with red paint splatter"></div>
  <div class="abs cover" style="left:844px;background:linear-gradient(135deg,#222 0%,#8c96a8 45%,#3a3a3a 100%)" role="img" aria-label="Horror book cover with frightened figure"></div>
  <div class="abs caption" style="left:138px"><span>Novel Tittle</span><b>$50.00</b></div>
  <div class="abs caption" style="left:373px"><span>Novel Tittle</span><b>$35.00</b></div>
  <div class="abs caption" style="left:609px"><span>Novel Tittle</span><b>$60.00</b></div>
  <div class="abs caption" style="left:844px"><span>Novel Tittle</span><b>$40.00</b></div>
</section>

<section class="abs newsletter">
  <h2>Sign Up for Newsletters</h2>
  <div class="abs email">Email address</div>
  <div class="abs subscribe">Subscribe</div>
</section>

<section>
  <div class="abs tile" style="left:118px;background:linear-gradient(160deg,#a58f86,#6e5a52 60%,#8a6a52)" role="img" aria-label="Photo of a woman writing at a table">
    <h3>OTHER WORK</h3><div class="band" style="background:rgba(112,0,181,.85)">VIEW MY WORK</div>
  </div>
  <div class="abs tile" style="left:450px;background:radial-gradient(circle at 50% 30%,#c9a24a,#6a4a18 55%,#2a1a08)" role="img" aria-label="Photo of a lit wall lamp">
    <h3>MY BLOGS</h3><div class="band" style="background:rgba(240,235,220,.85);color:#111">LEARN MORE</div>
  </div>
  <div class="abs tile" style="left:781px;background:radial-gradient(circle at 55% 60%,#e8a050,#8a3a18 50%,#1a0a06)" role="img" aria-label="Photo of a hand in warm firelight">
    <h3>RESOURCES</h3><div class="band" style="background:rgba(60,0,110,.85)">VIEW MY WORK</div>
  </div>
</section>

<footer class="abs footer">
  <nav class="abs footer-nav"><span>Home</span><span>Books</span><span>Blog</span><span>Resources</span><span>Other works</span><span>Store</span></nav>
  <p class="abs copyright">© 2017 Company Name &nbsp;All right reserved &nbsp;Term of Use</p>
  <div class="abs social"><span>Flitter</span><span>Pagebook</span><span>Linkwork</span><span>Orbitplus</span></div>
</footer>

</body>
</html>
```